The design should look similar to the uploaded example to accommodate the information needed for a business card template. I would like to see the colors orange and charcoal grey incorporated along with the logo.The following should be on the back of the card SPECIALIZING IN NEW AND USED TIRES & WHEELS FOR:- Loaders- Skid Steers- Telehandlers- Boom Lifts- Forklifs and moreELIMINATING DOWNTIMEWheel Exchange Program for New & Used Foam Filled and Solid Rubber TiresSPECIALTY SERVICES- Foam Filling Tires- Largest Tire Press in SE- ONSITE Forklift Tire Press- Boom Truck Services - Rubber Tracks

Target Market(s)

New and Existing Customers

Industry/Entity Type

Business

Contact Information for Business Card

NAMEHEAVY DUTY TIRE, LLC8470 Belvedere RoadWest Palm Beach, FL 33411P: 844-HD-TIRESF: 561-431-6469C:E: W: WWW.GRANITERIMSUPPLY-EXAMPLE.COM

Font styles to use
Sans Serif

Colors
f37122
333333

Requirements
Must have
• The logo and the information indicated for the backside of the card
Nice to have
• Keep the orange and charcoal grey colors

```html
<!DOCTYPE html>
<html lang="en">
<head>
<meta charset="utf-8">
<title>Granite Rim Supply business card</title>
<link rel="stylesheet" href="https://fonts.googleapis.com/css2?family=Roboto+Slab:wght@700&family=PT+Sans:ital,wght@0,400;0,700;1,400&display=swap">
<style>
  :root {
    --charcoal: #333d47;
    --charcoal-deep: #2e3339;
    --orange: #e0732f;
    --paper: #f1f1f2;
    --ink: #3a3f45;
    --backdrop: #a3a3a3;
    --white: #ffffff;
  }
  * { box-sizing: border-box; margin: 0; padding: 0; }
  html, body { width: 1105px; height: 1200px; overflow: hidden; }
  body {
    background: var(--backdrop);
    font-family: "PT Sans", Arial, sans-serif;
    position: relative;
  }
  .card {
    position: absolute;
    left: 182px;
    width: 747px;
    height: 427px;
    overflow: hidden;
  }
  /* Front */
  .card-front { top: 119px; background: var(--paper); }
  .brand {
    position: absolute;
    left: 62px; top: 180px;
    display: flex; align-items: center; gap: 14px;
  }
  .brand-dot {
    width: 56px; height: 56px; border-radius: 50%;
    background: var(--orange);
  }
  .brand-name {
    font-family: "Roboto Slab", Georgia, serif;
    font-weight: 700; font-size: 22px; line-height: 1.15;
    color: var(--charcoal-deep); letter-spacing: 0.5px;
  }
  .divider {
    position: absolute; left: 374px; top: 68px;
    width: 1px; height: 270px; background: #c9cacc;
  }
  .contact { position: absolute; left: 404px; top: 64px; color: var(--ink); }
  .person-name {
    font-family: "Roboto Slab", Georgia, serif;
    font-weight: 700; font-size: 29px; line-height: 1.05;
    color: var(--charcoal); letter-spacing: 0.5px;
  }
  .person-title {
    font-family: "Roboto Slab", Georgia, serif;
    font-weight: 700; font-size: 19px; color: var(--orange);
    margin-top: 2px; letter-spacing: 0.3px;
  }
  .address { font-size: 20px; line-height: 27px; margin-top: 20px; }
  .details { list-style: none; margin-top: 12px; font-size: 20px; }
  .details li { display: flex; align-items: center; gap: 10px; height: 28px; }
  .details svg { width: 18px; height: 18px; fill: var(--charcoal); flex: none; }
  .rule-orange {
    position: absolute; left: 0; right: 0; top: 391px;
    height: 3px; background: var(--orange);
  }
  .band-charcoal {
    position: absolute; left: 0; right: 0; top: 398px; bottom: 0;
    background: var(--charcoal);
  }
  /* Back */
  .card-back { top: 637px; background: var(--orange); }
  .tire-mark {
    position: absolute; left: -30px; top: 18px;
    width: 386px; height: 386px; border-radius: 50%;
    background: var(--charcoal-deep);
  }
  .services {
    position: absolute; right: 35px; top: 36px;
    text-align: right; color: var(--white);
  }
  .services h2 {
    font-weight: 700; font-size: 20px; line-height: 27px;
    text-transform: uppercase; letter-spacing: 0.2px;
  }
  .services p { font-size: 19.5px; line-height: 26px; }
  .services .list { font-style: italic; font-size: 20px; line-height: 27px; }
  .section + .section { margin-top: 19px; }
</style>
</head>
<body>
  <section class="card card-front" aria-label="Business card front">
    <div class="brand">
      <span class="brand-dot"></span>
      <span class="brand-name">GRANITE RIM<br>SUPPLY, LLC</span>
    </div>
    <div class="divider"></div>
    <div class="contact">
      <h1 class="person-name">DANIEL REYES</h1>
      <div class="person-title">CEO/FOUNDER</div>
      <p class="address">5126 Marston Lane<br>West Palm Beach, FL 33411</p>
      <ul class="details">
        <li><svg viewBox="0 0 24 24"><path d="M6.6 10.8a15 15 0 0 0 6.6 6.6l2.2-2.2c.3-.3.7-.4 1-.2 1.1.4 2.3.6 3.6.6.6 0 1 .4 1 1V20c0 .6-.4 1-1 1A17 17 0 0 1 3 4c0-.6.4-1 1-1h3.5c.6 0 1 .4 1 1 0 1.3.2 2.5.6 3.6.1.3 0 .7-.2 1z"/></svg>844-GR-WHEEL</li>
        <li><svg viewBox="0 0 24 24"><path d="M7 1h10a2 2 0 0 1 2 2v18a2 2 0 0 1-2 2H7a2 2 0 0 1-2-2V3a2 2 0 0 1 2-2zm0 3v14h10V4zm5 15.2a1.2 1.2 0 1 0 0 2.4 1.2 1.2 0 0 0 0-2.4z"/></svg>836 512 7740</li>
        <li><svg viewBox="0 0 24 24"><path d="M6 2h12v5H6zM3 8h18a2 2 0 0 1 2 2v7h-4v5H5v-5H1v-7a2 2 0 0 1 2-2zm4 8v4h10v-4z"/></svg>561-278-9053</li>
        <li><svg viewBox="0 0 24 24"><path d="M2 5h20v14H2zm2 2v.5l8 5 8-5V7zm0 2.8V17h16V9.8l-8 5z"/></svg>info@granite-example.com</li>
        <li><svg viewBox="0 0 24 24"><path d="M12 2a10 10 0 1 0 0 20 10 10 0 0 0 0-20zm-1 17.9A8 8 0 0 1 4.2 10l4.8 4.8v1a2 2 0 0 0 2 2zm6.9-2.5A2 2 0 0 0 16 16h-1v-3a1 1 0 0 0-1-1H8v-2h2a1 1 0 0 0 1-1V7h2a2 2 0 0 0 2-2v-.4a8 8 0 0 1 2.9 12.8z"/></svg>www.graniterimsupply-example.com</li>
      </ul>
    </div>
    <div class="rule-orange"></div>
    <div class="band-charcoal"></div>
  </section>

  <section class="card card-back" aria-label="Business card back">
    <div class="tire-mark" role="img" aria-label="Large brand tire mark"></div>
    <div class="services">
      <div class="section">
        <h2>Specializing in new and<br>used tires &amp; wheels for</h2>
        <p class="list">Loaders • Skid Steers • Telehandlers •<br>Boom Lifts • Forklifs and more •</p>
      </div>
      <div class="section">
        <h2>Eliminating downtime</h2>
        <p>Wheel Exchange Program for New &amp;<br>Used Foam Filled &amp; Solid Rubber Tires</p>
      </div>
      <div class="section">
        <h2>Specialty services</h2>
        <p class="list">Foam Filling Tires •<br>Largest Tire Press in SE •<br>ONSITE Forklift Tire Press •<br>Boom Truck Services • Rubber Tracks •</p>
      </div>
    </div>
  </section>
</body>
</html>
```